Cover for a Non-Fiction Book on Authoritarianism for a Washington D.C. Think Tank

Create a dynamic and engaging cover highlighting the role of contemporary and historical authoritarianism for a non-fiction edited volume. The book brings together chapters from many leading academics on the subject. The tone should be serious but provocative. Proprietary images are not acceptable as we are not budgeting for licensing. The books dimensions are 6x9. Preference will be given to designers with front and back cover design with sample ipsum lorum text.

One of covers that we particularly liked was "When Quiet Crowds Prevail" a link to the image on shelvora is: http://www.shelvora.example/s/ref=nb_sb_noss/190-2603447-3311705?url=search-alias%3Daps&field-keywords=When+Quiet+Crowds+Prevail

Attached is a draft version of the manuscript to assist in shaping your creative vision.

Project Deadline Extended Reason: I have extended the deadline at the request of the editors. They would like to see some designs that rely less heavily on the themes of fists and barbed wire to reference authoritarianism. I apologize to designs with current submissions, some of them are very professional, however none of the designs are currently under consideration for use. Added Saturday, January 24, 2015

Project Deadline Extended Reason: Editors are still unsatisfied with current sample of options. I apologize to those current contributors, but anything challenging and new would be well received. Added Friday, January 30, 2015

Project Deadline Extended Reason: I've updated the deadline so that designers that were well ranked can submit full front and back covers to assist the book editors in making their final decision. Added Friday, February 13, 2015

Font styles to use
Serif
Sans Serif

Requirements
Must have
• 1) Title: Are Strongmen Quietly Returning Again
• 2) Editors: Dorian Kettleby and Lucia R. Venhorst
• 3) Language from client: "a simple design that captured both a symbol of repression and resistance would be ideal. The cover of When Quiet Crowds Prevail is a great example. Nothing busy or overly complicated. The image of mass street protests may be overused at this point so I'd opt for something a bit more creative. Vibrant colors always great."
• 4) This final project design must use the attached InDesign template file when constructing the cover (IDML and INDD versions of the template are available).
Nice to have
• Feel free to use Meridale Forum logo designs pulled from the web.
Should not have
• Photographs that would require compensating a copyright holder.

```html
<!DOCTYPE html>
<html lang="en">
<head>
<meta charset="utf-8">
<title>Are Strongmen Quietly Returning Again — Book Cover</title>
<link rel="stylesheet" href="https://fonts.googleapis.com/css2?family=Montserrat:wght@400;700;800&display=swap">
<style>
  :root {
    --cover-red: #fe0000;
    --cover-glow: #ff3a14;
    --ink: #000000;
    --paper: #ffffff;
    --shadow-ink: #120202;
  }
  * { margin: 0; padding: 0; box-sizing: border-box; }
  html, body {
    width: 796px;
    height: 1200px;
    overflow: hidden;
    background: var(--cover-red);
  }
  .cover {
    position: relative;
    width: 796px;
    height: 1200px;
    overflow: hidden;
    background: radial-gradient(ellipse 420px 360px at 400px 780px, var(--cover-glow) 0%, var(--cover-red) 100%);
    font-family: "Montserrat", Arial, sans-serif;
    color: var(--ink);
  }
  .cover-art {
    position: absolute;
    left: 52px;
    top: 28px;
    width: 698px;
    height: 484px;
    border-radius: 349px 349px 40px 40px;
    background: linear-gradient(180deg, var(--shadow-ink) 0%, var(--shadow-ink) 55%, #3a0404 100%);
  }
  .title-block { font-size: 0; }
  .title {
    position: absolute;
    left: 0;
    width: 100%;
    text-align: center;
    font-weight: 800;
    text-transform: uppercase;
    line-height: 1;
    white-space: nowrap;
  }
  .title-lead {
    top: 688px;
    font-size: 96px;
    letter-spacing: 1px;
  }
  .title-main {
    top: 850px;
    font-size: 60px;
    letter-spacing: 0.5px;
  }
  .title-band {
    position: absolute;
    left: 0;
    top: 918px;
    width: 796px;
    height: 84px;
  }
  .title-band svg {
    position: absolute;
    inset: 0;
  }
  .title-band-text {
    position: absolute;
    left: 0;
    top: 13px;
    width: 100%;
    text-align: center;
    font-weight: 800;
    font-size: 60px;
    line-height: 1;
    letter-spacing: 0.5px;
    white-space: nowrap;
  }
  .editors {
    position: absolute;
    left: 0;
    top: 1046px;
    width: 100%;
    text-align: center;
    font-weight: 400;
    font-size: 22px;
    color: var(--ink);
  }
  .publisher {
    position: absolute;
    left: 0;
    top: 1118px;
    width: 100%;
    display: flex;
    justify-content: center;
    align-items: center;
    gap: 10px;
    color: var(--paper);
    font-weight: 700;
    font-size: 32px;
    line-height: 1;
  }
  .publisher-mark {
    width: 30px;
    height: 30px;
    border-radius: 50%;
    background: var(--paper);
  }
</style>
</head>
<body>
  <main class="cover">
    <div class="cover-art" role="img" aria-label="Large black silhouette artwork filling the upper half of the cover"></div>

    <h1 class="title-block">
      <span class="title title-lead">Are</span>
      <span class="title title-main">Strongmen Quietly</span>
    </h1>

    <div class="title-band">
      <svg width="796" height="84" viewBox="0 0 796 84" aria-hidden="true">
        <polygon fill="#ffffff" points="0,6 40,3 90,7 150,2 210,6 280,3 340,7 410,2 480,6 550,3 620,7 690,2 750,6 796,3 796,80 760,83 700,79 640,84 570,80 500,83 430,79 360,84 290,80 220,83 150,79 80,84 30,80 0,83"/>
      </svg>
      <p class="title title-band-text">Returning Again?</p>
    </div>

    <p class="editors">Dorian Kettleby and Lucia R. Venhorst</p>

    <div class="publisher">
      <span class="publisher-mark" aria-hidden="true"></span>
      <span class="publisher-name">Meridale Forum</span>
    </div>
  </main>
</body>
</html>
```